Looking for a modern, Professional business card design

We have a simple business card, but are looking for a more modern, professional look. A sample of the basic card is attached as well as the logo. We would also like to add that we offer:
Struggling with your finances?
- Learn to become debt free
- Discover the power of cash
- Control your money instead of it controlling you
Let us help you achieve a new level of financial freedom!
Also, we would like to have a "SPECIAL OFFER!: FREE 30 minute consultation"
Financial Planning

```html
<!DOCTYPE html>
<html lang="en">
<head>
<meta charset="utf-8">
<title>Brightpath Coaching – Business Card</title>
<link href="https://fonts.googleapis.com/css2?family=Open+Sans:wght@400;600;700&display=swap" rel="stylesheet">
<style>
  :root {
    --backdrop: #e4e2df;
    --card: #070707;
    --card-glow: #141414;
    --green: #4a9e3c;
    --green-bright: #7cc242;
    --text: #ffffff;
    --rule: #d8d8d8;
  }
  * { margin: 0; padding: 0; box-sizing: border-box; }
  html, body {
    width: 1200px; height: 1000px; overflow: hidden;
    background: var(--backdrop);
    font-family: "Open Sans", Arial, sans-serif;
    color: var(--text);
  }
  .card {
    position: absolute; left: 265px; width: 666px; height: 397px;
    background: radial-gradient(ellipse at 30% 45%, var(--card-glow), var(--card) 70%);
    box-shadow: 0 6px 14px rgba(0,0,0,.35);
  }
  .card--front { top: 73px; }
  .card--back { top: 532px; }

  .brand {
    position: absolute; display: flex; align-items: center; gap: 10px;
    font-weight: 700; font-size: 27px; color: var(--text); white-space: nowrap;
  }
  .brand__dot { width: 22px; height: 22px; border-radius: 50%; background: var(--green-bright); }
  .card--front .brand { right: 32px; top: 84px; }
  .card--back .brand { left: 32px; top: 84px; }

  .holder { position: absolute; left: 33px; top: 193px; }
  .holder__name { font-size: 24px; font-weight: 600; color: var(--green); line-height: 1.2; }
  .holder__role { font-size: 16px; line-height: 1.35; }

  .contact { position: absolute; right: 32px; top: 189px; text-align: right; font-size: 16px; white-space: nowrap; }
  .contact__line { display: flex; justify-content: flex-end; align-items: center; gap: 8px; height: 22.7px; }
  .contact__line svg { width: 16px; height: 16px; fill: var(--green); }
  .contact__address { margin-top: 5px; height: 22px; }

  .offer {
    position: absolute; right: 32px; top: 318px; width: 264px;
    border-top: 1px solid var(--rule); padding-top: 10px; text-align: right;
    font-size: 16px; line-height: 21px;
  }
  .offer__title { font-weight: 700; }

  .pitch { position: absolute; left: 342px; top: 200px; width: 300px; font-size: 16px; line-height: 20px; }
  .pitch__title { font-weight: 700; margin-bottom: 11px; }
  .pitch__list { list-style: none; }
  .pitch__list li { display: flex; gap: 5px; margin-bottom: 6px; }
  .pitch__list svg { flex: none; width: 14px; height: 14px; margin-top: 4px; }
  .pitch__close { margin-top: 2px; }
</style>
</head>
<body>
  <section class="card card--front">
    <div class="brand"><span class="brand__dot"></span>Brightpath Coaching</div>

    <div class="holder">
      <p class="holder__name">Adrian Novak</p>
      <p class="holder__role">Managing Director</p>
    </div>

    <div class="contact">
      <p class="contact__line">+ 000 000 0000
        <svg viewBox="0 0 16 16"><path d="M4 0h8v16H4z M5 2v10h6V2z M7 13h2v1H7z" fill-rule="evenodd"/></svg></p>
      <p class="contact__line">+ 000 000 0000
        <svg viewBox="0 0 16 16"><path d="M1 6c0-3 14-3 14 0v2h-3V6H4v2H1z M3 9h10l1 5H2z"/></svg></p>
      <p class="contact__line">info@brightpathcoach.com
        <svg viewBox="0 0 16 16"><path d="M1 3h14v10H1z M2 4l6 5 6-5z" fill-rule="evenodd"/></svg></p>
      <p class="contact__line">www.brightpathcoach.com
        <svg viewBox="0 0 16 16"><path d="M8 1a7 7 0 1 0 0 14A7 7 0 0 0 8 1z M8 3a5 5 0 1 1 0 10A5 5 0 0 1 8 3z M3 7h10v2H3z M7 3h2v10H7z" fill-rule="evenodd"/></svg></p>
      <p class="contact__address">18 Harbor 40 Ave, Fairhaven, OR 97512</p>
    </div>

    <div class="offer">
      <p class="offer__title">SPECIAL OFFER!:</p>
      <p>FREE 30 minute consultation</p>
    </div>
  </section>

  <section class="card card--back">
    <div class="brand"><span class="brand__dot"></span>Brightpath Coaching</div>

    <div class="pitch">
      <p class="pitch__title">Struggling with your finances?</p>
      <ul class="pitch__list">
        <li><svg viewBox="0 0 14 14"><path d="M1 7l4 5L13 1" fill="none" stroke="#7cc242" stroke-width="2"/></svg>Learn to become debt free</li>
        <li><svg viewBox="0 0 14 14"><path d="M1 7l4 5L13 1" fill="none" stroke="#7cc242" stroke-width="2"/></svg>Discover the power of cash</li>
        <li><svg viewBox="0 0 14 14"><path d="M1 7l4 5L13 1" fill="none" stroke="#7cc242" stroke-width="2"/></svg>Control your money instead of it controlling you</li>
      </ul>
      <p class="pitch__close">Let us help you achieve a new level of financial freedom!</p>
    </div>
  </section>
</body>
</html>
```